Custom Woodworking and Rock Design

We specialize in original, high quality, wood and rock art. It’s should be self explanatory ask questions if you need. Your team designing a logo. Furniture is custom made to order. Rocks are designed depending on consumer needs. Wood and rock can also be combined for custom work. Painted rocks on vintage wood. Custom chairs and cabinets. Artistic rocks for multiple uses:garden, magnets, custom. All ideas and requests are welcome.

Target Market(s)

All

Contact Information for Business Card

Mara Voss
Talbertstonecraft@mailbrook.net

Font styles to use
Sans Serif

Requirements
Must have
• Clear lettering
Nice to have
• Eye catching
Should not have
• Blurr

```html
<!DOCTYPE html>
<html lang="en">
<head>
<meta charset="utf-8">
<title>Talbert Stonecraft – Business Card</title>
<link href="https://fonts.googleapis.com/css2?family=Open+Sans:wght@400;600&display=swap" rel="stylesheet">
<style>
  :root {
    --stage: #8a8889;
    --card-dark: #3e3e40;
    --card-light: #5a5a5c;
    --brand-red: #e8262c;
    --tan: #c9a57a;
  }
  * { box-sizing: border-box; margin: 0; padding: 0; }
  html, body { width: 1200px; height: 880px; overflow: hidden; }
  body {
    background: var(--stage);
    font-family: "Open Sans", sans-serif;
    display: flex;
    flex-direction: column;
    align-items: center;
    justify-content: center;
    gap: 40px;
  }
  .card {
    position: relative;
    width: 640px;
    height: 366px;
    border-radius: 22px;
    background: linear-gradient(135deg, var(--card-dark) 0%, var(--card-light) 50%, var(--card-dark) 100%);
  }
  .wordmark {
    display: flex;
    align-items: center;
    gap: 10px;
    color: var(--brand-red);
    font-weight: 600;
    text-transform: uppercase;
    white-space: nowrap;
  }
  .wordmark .mark {
    background: var(--brand-red);
    flex: none;
  }
  .card-front .wordmark {
    position: absolute;
    left: 50%; top: 50%;
    transform: translate(-50%, -50%);
    font-size: 30px;
    letter-spacing: 0.5px;
  }
  .card-front .mark { width: 26px; height: 26px; }
  .card-back .wordmark {
    position: absolute;
    right: 44px; top: 92px;
    font-size: 20px;
  }
  .card-back .mark { width: 18px; height: 18px; }
  .identity {
    position: absolute;
    left: 48px; top: 150px;
  }
  .identity .name {
    color: var(--tan);
    font-size: 21px;
    font-weight: 600;
    text-transform: uppercase;
    letter-spacing: 0.5px;
  }
  .identity .role {
    color: var(--brand-red);
    font-size: 17px;
    margin-top: -2px;
  }
  .contacts {
    position: absolute;
    left: 48px; top: 238px;
    list-style: none;
    display: flex;
    flex-direction: column;
    gap: 8px;
  }
  .contacts li {
    display: flex;
    align-items: center;
    gap: 12px;
    color: var(--tan);
    font-size: 17px;
    white-space: nowrap;
  }
  .contacts svg { width: 24px; height: 20px; flex: none; }
</style>
</head>
<body>
  <section class="card card-front" aria-label="Card front">
    <div class="wordmark"><span class="mark"></span>Talbert Stonecraft</div>
  </section>

  <section class="card card-back" aria-label="Card back">
    <div class="wordmark"><span class="mark"></span>Talbert Stonecraft</div>
    <div class="identity">
      <p class="name">Mara Voss</p>
      <p class="role">Director</p>
    </div>
    <ul class="contacts">
      <li>
        <svg viewBox="0 0 24 20" aria-hidden="true"><path fill="#e8262c" d="M2 6c0-2 4-4 10-4s10 2 10 4v2h-5V6H7v2H2z M5 9h14l2 9H3z"/><circle cx="12" cy="13" r="2.5" fill="#3e3e40"/></svg>
        555-318-2046
      </li>
      <li>
        <svg viewBox="0 0 24 20" aria-hidden="true"><rect x="1" y="3" width="22" height="14" fill="#e8262c"/><path d="M1 3l11 8 11-8" fill="none" stroke="#3e3e40" stroke-width="1.6"/></svg>
        Talbertstonecraft@mailbrook.net
      </li>
      <li>
        <svg viewBox="0 0 24 20" aria-hidden="true"><rect x="2" y="1" width="20" height="13" fill="none" stroke="#e8262c" stroke-width="2"/><rect x="9" y="15" width="6" height="2" fill="#e8262c"/><rect x="6" y="17" width="12" height="2" fill="#e8262c"/></svg>
        www.talbertstonecraft.net
      </li>
    </ul>
  </section>
</body>
</html>
```